real esate business card with company logo and name

we need a business card design for a real esate company

The company name is Walsh & Brand Pty Ltd, and we have our logo designed and will upload. We want classic or moden feel. Black or white background. looks more textured. Should include folowinginformations
Owen Walsh and Lucy Brand
Sales Agents & Onsite Manager
p: 07 5948 2063
F: 07 5948 2174
M:0431 857 219
3/42 Marlow Crescent, FERNLEA QLD 4213

We want this business card looks professonal. Thank you in advance.

Industry/Entity Type

Real Estate Agent

Contact Information for Business Card

Owen Walsh and Lucy Brand
Onsite Manager & Sales Agents
p: 07 5948 2063
M:0431 857 219

Font styles to use
Serif

Colors
000000
fbfbfb
333333
959595

Requirements
Must have
• company logo and name, black or white back ground

```html
<!DOCTYPE html>
<html lang="en">
<head>
<meta charset="utf-8">
<title>Walsh &amp; Brand Pty Ltd — Business Card</title>
<link rel="stylesheet" href="https://fonts.googleapis.com/css2?family=Cormorant+SC:wght@500;600&display=swap">
<style>
  :root {
    --ink: #000000;
    --paper: #fbfbfb;
    --charcoal: #333333;
    --grey: #959595;
    --stage: #e9e9e7;
    --silver-light: #f2f2f2;
    --silver-mid: #c9c9c9;
    --silver-dark: #8e8e8e;
  }
  * { box-sizing: border-box; margin: 0; padding: 0; }
  html, body { width: 1200px; height: 913px; overflow: hidden; }
  body {
    background: var(--stage);
    font-family: "Cormorant SC", "Times New Roman", serif;
    color: var(--charcoal);
    position: relative;
  }
  .card {
    position: absolute;
    top: 308px;
    width: 520px;
    height: 297px;
    border-radius: 14px;
    overflow: hidden;
    box-shadow: 0 10px 24px rgba(0,0,0,.18);
  }

  /* ---------- Front ---------- */
  .card--front {
    left: 60px;
    background:
      repeating-radial-gradient(circle at 30% 40%, rgba(0,0,0,.025) 0 1px, transparent 1px 3px),
      var(--paper);
  }
  .edge-band {
    position: absolute; top: 0; bottom: 0; left: 0;
    width: 26px; background: var(--ink);
  }
  .edge-bevel {
    position: absolute; top: 0; bottom: 0; left: 26px;
    width: 14px;
    background: linear-gradient(90deg, var(--silver-dark), var(--silver-light) 45%, var(--silver-mid));
  }
  .agent-block { position: absolute; left: 62px; top: 40px; }
  .agent-names {
    font-size: 23px; font-weight: 600; color: var(--ink);
    letter-spacing: .5px; line-height: 1;
  }
  .agent-role {
    font-size: 14px; font-weight: 500; color: var(--grey);
    margin-top: 6px; letter-spacing: .4px;
  }
  .agent-address {
    font-size: 14px; font-weight: 600; color: var(--charcoal);
    margin-top: 8px; line-height: 1.2;
  }
  .contact-list {
    position: absolute; left: 62px; bottom: 34px;
    list-style: none; font-size: 14px; font-weight: 600; color: var(--charcoal);
  }
  .contact-list li { display: flex; align-items: center; gap: 8px; line-height: 1.35; }
  .contact-icon { width: 11px; height: 11px; fill: var(--charcoal); }

  .brand-block {
    position: absolute; right: 34px; top: 70px; width: 200px;
    display: flex; flex-direction: column; align-items: center; gap: 14px;
  }
  .brand-square {
    width: 62px; height: 62px;
    background: linear-gradient(135deg, var(--silver-mid), var(--silver-dark));
  }
  .brand-name {
    font-size: 20px; font-weight: 600; color: var(--grey);
    letter-spacing: 1px; text-align: center; white-space: nowrap;
  }

  /* ---------- Back ---------- */
  .card--back {
    left: 620px;
    background:
      repeating-radial-gradient(circle at 60% 50%, rgba(255,255,255,.06) 0 1px, transparent 1px 3px),
      linear-gradient(160deg, #d7d7d7, #b9b9b9 40%, #e4e4e4 70%, #a9a9a9);
  }
  .card--back .edge-band {
    left: auto; right: 0; width: 22px;
    background: linear-gradient(90deg, #555, var(--ink));
  }
  .card--back .edge-bevel {
    left: auto; right: 22px; width: 14px;
    background: linear-gradient(90deg, var(--silver-mid), var(--silver-light) 55%, var(--silver-dark));
  }
  .card--back .brand-block {
    right: auto; left: 0; width: 484px; top: 84px; gap: 18px;
  }
  .card--back .brand-square {
    width: 70px; height: 70px;
    background: linear-gradient(135deg, #efefef, var(--silver-dark));
  }
  .card--back .brand-name { color: var(--charcoal); font-size: 22px; }
</style>
</head>
<body>

  <section class="card card--front" aria-label="Business card front">
    <div class="edge-band"></div>
    <div class="edge-bevel"></div>

    <div class="agent-block">
      <h1 class="agent-names">Owen Walsh &amp; Lucy Brand</h1>
      <p class="agent-role">Sales Agents &amp; Onsite Manager</p>
      <p class="agent-address">3/42 Marlow Crescent<br>FERNLEA QLD 4213</p>
    </div>

    <ul class="contact-list">
      <li>
        <svg class="contact-icon" viewBox="0 0 24 24" aria-label="Phone"><path d="M6.6 10.8a15 15 0 0 0 6.6 6.6l2.2-2.2a1 1 0 0 1 1-.25 11.4 11.4 0 0 0 3.6.57 1 1 0 0 1 1 1V20a1 1 0 0 1-1 1A17 17 0 0 1 3 4a1 1 0 0 1 1-1h3.5a1 1 0 0 1 1 1c0 1.25.2 2.45.57 3.6a1 1 0 0 1-.25 1z"/></svg>
        07 5948 2063
      </li>
      <li>
        <svg class="contact-icon" viewBox="0 0 24 24" aria-label="Fax"><path d="M6 2h10v6H6zM3 9h18v10h-3v3H6v-3H3zm5 7v4h8v-4z"/></svg>
        07 5948 2174
      </li>
      <li>
        <svg class="contact-icon" viewBox="0 0 24 24" aria-label="Mobile"><path d="M7 1h10a2 2 0 0 1 2 2v18a2 2 0 0 1-2 2H7a2 2 0 0 1-2-2V3a2 2 0 0 1 2-2zm0 3v14h10V4zm5 15.5a1.2 1.2 0 1 0 0 2.4 1.2 1.2 0 0 0 0-2.4z"/></svg>
        0431 857 219
      </li>
    </ul>

    <div class="brand-block">
      <div class="brand-square"></div>
      <p class="brand-name">Walsh &amp; Brand Pty Ltd.</p>
    </div>
  </section>

  <section class="card card--back" aria-label="Business card back">
    <div class="edge-bevel"></div>
    <div class="edge-band"></div>
    <div class="brand-block">
      <div class="brand-square"></div>
      <p class="brand-name">Walsh &amp; Brand Pty Ltd.</p>
    </div>
  </section>

</body>
</html>
```